House flipping business web site needed

pinecrestholdingsgroup.example.
I am a residential developer in Northern NJ and I am looking for a fresh new updated website. I have an intro video about my company being made now. I don't update it very often but I want an easy format that I can add update photos to on projects I have worked on or homes I renovate for sale.

Target Market(s)

investors into my projects so a portfolio , people looking to sell their homes to me.

Industry/Entity Type

Real Estate Development

Number of Pages Required

4 page

Font styles to use
Serif

Colors
33b8a4
39a9d7
cadf82

Requirements
Must have
• space for an intro video about my company
• a portfolio with pictures and information about each project
• Markets we serve- Morris County, NJ
• My logo- already created
• SEO
• Yes I would like this to function over all platforms. Phone, computer, all platforms.
• history and background page
• I am looking for a completed page that I can upload to the site that hosts my website
Nice to have
• I want something creative, easy to navigate. modern.

```html
<!DOCTYPE html>
<html lang="en">
<head>
<meta charset="utf-8">
<title>Pinecrest Holdings Group</title>
<link rel="stylesheet" href="https://fonts.googleapis.com/css2?family=Roboto:wght@300;400;500;700&family=Open+Sans:wght@400;600;700&display=swap">
<style>
:root{
  --teal:#33b8a4;
  --blue:#39a9d7;
  --lime:#cadf82;
  --ink:#333;
  --body:#666;
  --muted:#999;
  --soft:#f5f6f8;
  --footer:#2b2b2b;
  --white:#fff;
}
*{margin:0;padding:0;box-sizing:border-box}
html,body{width:1200px;height:2990px;overflow:hidden;background:var(--white)}
body{font-family:"Open Sans",Arial,sans-serif;color:var(--body);font-size:13px;line-height:1.9}
.page{position:relative;width:1200px;height:2990px;overflow:hidden}
.abs{position:absolute}
h2.section-title{position:absolute;left:0;width:1200px;text-align:center;font-family:"Roboto",Arial,sans-serif;font-weight:400;font-size:22px;color:var(--ink);letter-spacing:.5px;text-transform:uppercase}
h2 .accent,h3 .accent{color:var(--blue)}
.section-sub{position:absolute;left:0;width:1200px;text-align:center;font-size:12px;color:var(--body)}

/* header */
.top-line{left:0;top:0;width:1200px;height:4px;background:linear-gradient(90deg,var(--lime),var(--teal),var(--blue))}
.brand{left:86px;top:20px;display:flex;align-items:center;gap:12px;font-family:"Roboto",Arial,sans-serif;font-weight:500;font-size:24px;color:var(--teal);letter-spacing:1px}
.brand .dot{width:44px;height:44px;border-radius:50%;background:var(--teal)}
.top-contact{right:86px;top:22px;font-family:"Roboto",Arial,sans-serif;font-size:14px;color:var(--blue);display:flex;gap:34px}
.top-contact span{display:flex;align-items:center;gap:8px}
.main-nav{right:86px;top:68px;display:flex;gap:0;font-family:"Roboto",Arial,sans-serif;font-size:12px;font-weight:500;color:#444}
.main-nav a{color:inherit;text-decoration:none;padding:4px 0;margin-left:76px}
.main-nav a.active{color:var(--blue)}
.main-nav .search{margin-left:22px;padding-left:12px;border-left:1px solid #ddd;display:flex;align-items:center}

/* hero */
.hero{left:0;top:106px;width:1200px;height:492px;background:linear-gradient(180deg,#8fb86a 0%,#5f8a45 40%,#4d6e3a 70%,#3f5a30 100%)}
.hero-title{left:86px;top:336px;font-family:"Roboto",Arial,sans-serif;font-weight:500;font-size:30px;color:var(--white);letter-spacing:.5px}
.hero-text{left:86px;top:378px;width:440px;font-size:12.5px;color:var(--white);line-height:2.3}
.hero-dots{left:556px;top:458px;display:flex;gap:4px}
.hero-dots i{width:14px;height:14px;border-radius:50%;border:2px solid var(--white)}
.hero-dots i.on{background:var(--blue)}

/* services */
.service{top:712px;width:300px;text-align:center}
.service .circle{width:116px;height:116px;border-radius:50%;margin:0 auto;display:flex;align-items:center;justify-content:center;border:5px solid rgba(255,255,255,.8);box-shadow:0 0 0 3px currentColor}
.service h3{margin-top:20px;font-family:"Roboto",Arial,sans-serif;font-weight:400;font-size:14px;color:#555;letter-spacing:.5px}
.service p{margin-top:6px;font-size:12px;line-height:2.05}

/* about */
.about{left:0;top:980px;width:1200px;height:386px;background:var(--soft)}
.about h3,.lower h3{font-family:"Roboto",Arial,sans-serif;font-weight:400;font-size:22px;color:var(--ink);text-transform:uppercase}
.about-copy{left:86px;top:1018px;width:534px}
.about-copy p{font-size:12px;line-height:2.05;margin-top:16px}
.btn-blue{display:inline-block;background:var(--blue);color:var(--white);font-family:"Roboto",Arial,sans-serif;font-weight:500;font-size:13px;padding:9px 24px;border-radius:3px;text-decoration:none;box-shadow:0 2px 0 #2b86ad}
.video{left:660px;top:1026px;width:456px;height:294px;background:linear-gradient(180deg,#9fb782 0%,#6e8a5a 40%,#5f7fa0 60%,#2f4a66 100%)}
.play{left:198px;top:122px;width:60px;height:42px;border-radius:10px;background:#e52d27}

/* portfolio */
.grid{left:86px;top:1482px;width:1030px;display:grid;grid-template-columns:repeat(4,252px);grid-auto-rows:194px;gap:8px 7px}
.tile{position:relative}
.tile.feature{background:var(--blue);border:1px solid rgba(255,255,255,.6);outline:1px solid var(--blue);color:var(--white);text-align:center;padding:38px 24px 0}
.tile.feature h4{font-family:"Roboto",Arial,sans-serif;font-weight:400;font-size:15px;text-transform:uppercase}
.tile.feature p{font-size:12px;line-height:1.95;margin-top:4px}
.tile.feature .link{width:26px;height:26px;border-radius:50%;background:var(--white);margin:6px auto 0;display:flex;align-items:center;justify-content:center}

/* banner */
.banner{left:0;top:1920px;width:1200px;height:298px;background:linear-gradient(100deg,var(--lime) 0%,#8fcf8e 40%,var(--teal) 65%,var(--blue) 100%);text-align:center;color:var(--white)}
.banner h2{margin-top:50px;font-family:"Roboto",Arial,sans-serif;font-weight:300;font-size:28px;letter-spacing:.5px}
.banner p{width:740px;margin:18px auto 0;font-size:12px;line-height:2.05}
.btn-ghost{display:inline-block;margin-top:24px;border:2px solid var(--white);color:var(--white);font-family:"Roboto",Arial,sans-serif;font-size:13px;padding:10px 36px;border-radius:3px;text-decoration:none;text-transform:uppercase}

/* lower */
.what{left:86px;top:2252px;width:434px}
.what .photo{margin-top:22px;width:434px;height:184px;background:linear-gradient(180deg,#b9cbe0 0%,#d8d4c6 45%,#8d8a7c 75%,#6c7a4c 100%)}
.what p{margin-top:14px;font-size:12px;line-height:2.05}
.more-link{font-family:"Roboto",Arial,sans-serif;font-weight:700;font-size:12px;color:var(--blue);text-decoration:none;text-transform:uppercase}
.blog{left:600px;top:2252px;width:516px}
.post{display:flex;gap:24px;padding:20px 0 22px;border-bottom:1px solid #e5e5e5}
.post .thumb{width:152px;height:116px;flex:none;background:linear-gradient(180deg,#b8c8d8 0%,#d4cdbc 50%,#6e7a4c 100%)}
.post h4{font-family:"Roboto",Arial,sans-serif;font-weight:500;font-size:15px;color:var(--ink);text-transform:uppercase;line-height:1.3}
.post .meta{font-size:11px;font-style:italic;color:var(--muted);margin-top:8px;display:flex;gap:16px}
.post p{font-size:12px;line-height:2;margin-top:6px}

/* footer */
.footer{left:0;top:2674px;width:1200px;height:242px;background:var(--footer);color:#ccc}
.footer h5{font-family:"Roboto",Arial,sans-serif;font-weight:500;font-size:16px;color:var(--white);text-transform:uppercase}
.footer-brand{left:126px;top:62px;width:220px;display:flex;flex-direction:column;align-items:center;gap:14px;font-family:"Roboto",Arial,sans-serif;font-weight:500;font-size:24px;color:var(--white);text-align:center;line-height:1.2}
.footer-brand .dot{width:70px;height:70px;border-radius:50%;background:var(--teal)}
.f-contact{left:398px;top:48px;width:230px}
.f-contact ul{list-style:none;margin-top:14px}
.f-contact li{display:flex;gap:14px;font-size:11px;line-height:1.5;margin-bottom:12px;color:var(--white)}
.f-contact li svg{flex:none;margin-top:2px}
.f-news{left:630px;top:48px;width:220px}
.f-news p{font-size:11.5px;line-height:1.8;margin-top:14px;color:var(--white)}
.f-news .field{margin-top:16px;width:210px;height:32px;background:var(--white);font-size:11px;color:#777;padding:7px 10px}
.f-news .subscribe{margin-top:10px;display:inline-block;background:var(--blue);color:var(--white);font-size:10px;font-weight:600;padding:5px 10px;text-transform:uppercase}
.f-follow{left:906px;top:48px;width:200px}
.f-follow p{font-size:11.5px;line-height:1.8;margin-top:14px;color:var(--white)}
.socials{display:flex;gap:8px;margin-top:16px}
.socials i{width:34px;height:34px;border-radius:50%;border:2px solid var(--white)}
.copyright{left:0;top:2916px;width:1200px;height:74px;background:var(--teal);color:var(--white);font-size:12px;text-align:center;line-height:74px}
</style>
</head>
<body>
<div class="page">

  <header>
    <div class="abs top-line"></div>
    <div class="abs brand"><span class="dot"></span>PINECREST HOLDINGS GROUP</div>
    <div class="abs top-contact">
      <span><svg width="14" height="12" viewBox="0 0 14 12"><rect x="1" y="1" width="12" height="10" rx="1" fill="none" stroke="currentColor" stroke-width="1.6"/><path d="M1 2l6 5 6-5" fill="none" stroke="currentColor" stroke-width="1.4"/></svg>EMAIL : info@company.com</span>
      <span><svg width="13" height="13" viewBox="0 0 13 13"><rect width="13" height="13" rx="2" fill="currentColor"/><path d="M4 3l1.5 2-1 1c.6 1.2 1.3 1.9 2.5 2.5l1-1 2 1.5-1 1.5C6 10 3 7 2.5 4z" fill="#fff"/></svg>CALL US : (000)-121-1231</span>
    </div>
    <nav class="abs main-nav">
      <a class="active" href="#">HOME</a><a href="#">ABOUT US</a><a href="#">SERVICES</a><a href="#">PORTFOLIO</a><a href="#">CONTACT US</a>
      <span class="search"><svg width="10" height="10" viewBox="0 0 10 10"><circle cx="4" cy="4" r="3" fill="none" stroke="#444" stroke-width="1.4"/><path d="M6.3 6.3L9 9" stroke="#444" stroke-width="1.4"/></svg></span>
    </nav>
  </header>

  <section class="abs hero" role="img" aria-label="Photo of a renovated two-storey home with brick and white walls among tall trees and a green lawn"></section>
  <div class="abs hero-title">PINECREST HOLDINGS GROUP</div>
  <p class="abs hero-text">Pinecrest Holdings Group is a family run business with 3rd generation builders and renovators in the Morris County area.</p>
  <div class="abs hero-dots"><i></i><i></i><i class="on"></i><i></i><i></i></div>

  <h2 class="section-title" style="top:626px">Our <span class="accent">Services</span></h2>
  <p class="section-sub" style="top:664px">Pinecrest Holdings Group is a family run business with 3rd generation builders and renovators in the Morris County area.</p>

  <div class="abs service" style="left:100px">
    <div class="circle" style="background:var(--lime);color:var(--lime)">
      <svg width="50" height="44" viewBox="0 0 50 44"><path d="M25 4L4 22h6v18h30V22h6z" fill="#fff"/><rect x="17" y="24" width="7" height="7" fill="var(--lime)"/><rect x="26" y="24" width="7" height="7" fill="var(--lime)"/></svg>
    </div>
    <h3>HOUSE</h3>
    <p>Pinecrest Holdings Group is a family run business with 3rd generation builders and renovators in the Morris County area.</p>
  </div>
  <div class="abs service" style="left:450px">
    <div class="circle" style="background:var(--blue);color:var(--blue)">
      <svg width="48" height="40" viewBox="0 0 48 40"><path d="M6 13h32M30 5l9 8-9 8M42 27H10M18 19l-9 8 9 8" fill="none" stroke="#fff" stroke-width="4" stroke-linejoin="round"/></svg>
    </div>
    <h3>FLIPPING</h3>
    <p>Pinecrest Holdings Group is a family run business with 3rd generation builders and renovators in the Morris County area.</p>
  </div>
  <div class="abs service" style="left:800px">
    <div class="circle" style="background:var(--teal);color:var(--teal)">
      <svg width="50" height="42" viewBox="0 0 50 42"><rect x="17" y="3" width="16" height="8" rx="2" fill="none" stroke="#fff" stroke-width="3"/><rect x="4" y="10" width="42" height="28" rx="3" fill="#fff"/><rect x="21" y="19" width="8" height="6" fill="var(--teal)"/></svg>
    </div>
    <h3>BUSINESS</h3>
    <p>Pinecrest Holdings Group is a family run business with 3rd generation builders and renovators in the Morris County area.</p>
  </div>

  <section class="abs about"></section>
  <div class="abs about-copy">
    <h3>About <span class="accent">My Company</span></h3>
    <p>We are a team of experienced home buyers and renovators in the Morris County, NJ area. Our specialty is purchasing distressed homes and property. We then collaborate with the best talents in Northern New Jersey to renovate those properties and transform them into the best house in importantly we give provides a better way of life and hope for their future.</p>
    <p>We are a team of experienced home buyers and renovators in the Morris County, NJ area. Our specialty is purchasing distressed homes and property. We then collaborate with the best talents in Northern New Jersey to renovate those properties.</p>
    <p style="margin-top:30px"><a class="btn-blue" href="#">READ MORE</a></p>
  </div>
  <div class="abs video" role="img" aria-label="Intro video still of a calm lake with trees reflected on the water">
    <div class="abs play"><svg width="60" height="42" viewBox="0 0 60 42"><path d="M24 13l14 8-14 8z" fill="#fff"/></svg></div>
  </div>

  <h2 class="section-title" style="top:1392px">Project <span class="accent">Portfolio</span></h2>
  <p class="section-sub" style="top:1430px">Pinecrest Holdings Group is a family run business with 3rd generation builders and renovators in the Morris County area.</p>
  <div class="abs grid">
    <div class="tile feature">
      <h4>Pinecrest Holdings</h4>
      <p>Pinecrest Holdings Group is a family run business with 3rd generation builders and renovators in the Morris County area.</p>
      <div class="link"><svg width="14" height="14" viewBox="0 0 14 14"><path d="M6 8l2-2M5 6L3 8a2 2 0 003 3l2-2M9 8l2-2a2 2 0 00-3-3L6 5" fill="none" stroke="var(--blue)" stroke-width="1.6"/></svg></div>
    </div>
    <div class="tile" role="img" aria-label="Project photo: two-storey house exterior with lawn" style="background:linear-gradient(180deg,#d9dde3,#b9ac92 55%,#5c7a3c)"></div>
    <div class="tile" role="img" aria-label="Project photo: rear view of a house under renovation" style="background:linear-gradient(180deg,#e2e2e2,#bcae95 55%,#6e6458)"></div>
    <div class="tile" role="img" aria-label="Project photo: green sided house against a blue sky" style="background:linear-gradient(180deg,#8ec0e6,#5e7a72 50%,#49605a)"></div>
    <div class="tile" role="img" aria-label="Project photo: porch framing under construction" style="background:linear-gradient(180deg,#c9ccd0,#a88a68 55%,#7a6a58)"></div>
    <div class="tile" role="img" aria-label="Project photo: radiant floor heating tubing laid on a slab" style="background:linear-gradient(180deg,#5c86a8,#3d6a92 55%,#7a6c66)"></div>
    <div class="tile" role="img" aria-label="Project photo: basement interior with exposed framing" style="background:linear-gradient(180deg,#8a6a44,#c8a870 50%,#e0d8c0)"></div>
    <div class="tile" role="img" aria-label="Project photo: finished living room with fireplace" style="background:linear-gradient(180deg,#d8d2c4,#8a7c6a 55%,#4c4238)"></div>
  </div>

  <section class="abs banner" role="img" aria-label="Soft blurred house backdrop in green and blue tones">
    <h2>PINECREST HOLDINGS GROUP</h2>
    <p>We are a team of experienced home buyers and renovators in the Morris County, NJ area. Our specialty is purchasing distressed homes and property. We then collaborate with the best talents in Northern New Jersey to renovate those properties in importantly we give provides a better way of life and hope for their future.</p>
    <a class="btn-ghost" href="#">Click here for more info</a>
  </section>

  <section class="abs what lower">
    <h3>What <span class="accent">We Do</span></h3>
    <div class="photo" role="img" aria-label="Renovated house with deck and stone retaining wall"></div>
    <p>We are a team of experienced home buyers and renovators in the Morris County, NJ area. Our specialty is purchasing distressed homes and property. We then collaborate with the best talents in Northern New Jersey to renovate those proper a better way of life and hope for their future.</p>
    <p style="margin-top:16px"><a class="more-link" href="#">Read more &gt;&gt;</a></p>
  </section>

  <section class="abs blog lower">
    <h3>Latest <span class="accent">Blog</span></h3>
    <article class="post">
      <div class="thumb" role="img" aria-label="Blog photo of a renovated house exterior"></div>
      <div>
        <h4>Pinecrest Holdings Group</h4>
        <div class="meta"><span>2nd, 3rd Feb 2015</span><span>MARION HALE</span></div>
        <p>We are a team of experienced home buyers and renovators in purchasing distressed homes and property.</p>
      </div>
    </article>
    <article class="post">
      <div class="thumb" role="img" aria-label="Blog photo of a house before renovation"></div>
      <div>
        <h4>Pinecrest Holdings Group</h4>
        <div class="meta"><span>2nd, 3rd Feb 2015</span><span>MARION HALE</span></div>
        <p>We are a team of experienced home buyers and renovators in purchasing distressed homes and property.</p>
      </div>
    </article>
    <p style="margin-top:14px"><a class="more-link" href="#">View more &gt;&gt;</a></p>
  </section>

  <footer class="abs footer">
    <div class="abs footer-brand"><span class="dot"></span>PINECREST HOLDINGS GROUP</div>
    <div class="abs f-contact">
      <h5>Contact Us</h5>
      <ul>
        <li><svg width="12" height="12" viewBox="0 0 12 12"><path d="M2 1l2 3-1 1c.8 1.6 2 2.8 3.6 3.6l1-1 3 2-1.2 1.6C5 10.5 1.5 7 .8 2.2z" fill="#fff"/></svg>(000)-121-1231 (Phone)</li>
        <li><svg width="12" height="12" viewBox="0 0 12 12"><rect x="3" y="1" width="6" height="3" fill="#fff"/><rect x="1" y="4" width="10" height="5" fill="#fff"/><rect x="3" y="8" width="6" height="3" fill="#fff"/></svg>(000)-121-1231 (Fax)</li>
        <li><svg width="12" height="10" viewBox="0 0 12 10"><rect x="1" y="1" width="10" height="8" fill="none" stroke="#fff" stroke-width="1.4"/><path d="M1 1l5 4 5-4" fill="none" stroke="#fff" stroke-width="1.2"/></svg>info@pinecrestholdingsgroup.example</li>
        <li><svg width="12" height="14" viewBox="0 0 12 14"><path d="M6 1a4 4 0 00-4 4c0 3 4 8 4 8s4-5 4-8a4 4 0 00-4-4z" fill="#fff"/><circle cx="6" cy="5" r="1.5" fill="var(--footer)"/></svg>#254 lorem ipsum dummy text<br>Lorem ipsum</li>
      </ul>
    </div>
    <div class="abs f-news">
      <h5>Newsletter Signup</h5>
      <p>Register Your email address to get information about us</p>
      <div class="field">Email Address</div>
      <span class="subscribe">Subscribe</span>
    </div>
    <div class="abs f-follow">
      <h5>Follow Us</h5>
      <p>Sed ut perspiciatis unde omnis iste natus error sit voluptatem accusantium beatae vitae dicta sunt explicabo.</p>
      <div class="socials"><i></i><i></i><i></i><i></i><i></i></div>
    </div>
  </footer>
  <div class="abs copyright">© Copyright 2016 Pinecrest Holdings Group All Rights Reserved</div>

</div>
</body>
</html>
```